Web design for business website

I need a web design for a business website for one of our clients who is specialized in alarm management software. I would like you to design 3 web pages, one for each of the 3 pages. You need to process the corporate identity of our client to the web design. This means the colors of the logo (red and black) should definitely show up on all of the 3 pages. Find the logo file for the logo of our customer. To increase readability I suggest you use a white/light background. All suggestions are welcome.

Please kindly download atttached Webdesign.zip and read the project brief first. The project brief refers to all other files of the zip file. Your design must have exactly the same structure as the wireframes.
Updates

Target Market(s)

B2B, Alarm management

Industry/Entity Type

Business

Number of Pages Required

3 page

Requirements
Must have
• The web design must have exactly the same structure as the wireframes and needs to contain the colors of the company logo.

```html
<!DOCTYPE html>
<html lang="en">
<head>
<meta charset="utf-8">
<title>NORVENTA – Real-time reasoning solutions</title>
<link href="https://fonts.googleapis.com/css2?family=Lato:wght@300;400;700;900&display=swap" rel="stylesheet">
<style>
:root{
  --accent:#ea4a1c;
  --navy:#1d1a38;
  --navy-deep:#17152e;
  --ink:#2b2b2b;
  --muted:#555;
  --line:#dcdcdc;
  --paper:#ffffff;
  --mist:#f3f2f2;
  --footer:#e9e9eb;
}
*{box-sizing:border-box;margin:0;padding:0}
html,body{width:1200px;height:1125px;overflow:hidden;background:var(--paper);font-family:"Lato",Arial,sans-serif;color:var(--ink)}
.page{position:relative;width:1200px;height:1125px}
.wrap{position:absolute;left:269px;width:649px}

.topbar{position:absolute;top:0;left:0;width:1200px;height:27px;border-bottom:1px solid var(--line)}
.topbar .phone{position:absolute;left:270px;top:8px;font-size:9px;font-weight:700;color:#222}
.lang{position:absolute;left:733px;top:3px;width:53px;height:21px;border:1px solid #ccc;font-size:9px;font-weight:700;padding:5px 0 0 8px}
.lang::after{content:"";position:absolute;right:0;top:0;width:18px;height:19px;border-left:1px solid #ccc}
.lang span{position:absolute;right:5px;top:8px;border:4px solid transparent;border-top:5px solid #888;z-index:1}
.search{position:absolute;left:793px;top:3px;width:125px;height:21px;border:1px solid #ccc;font-size:9px;color:#999;padding:5px 7px}

.header{position:absolute;top:27px;left:0;width:1200px;height:68px;border-bottom:1px solid var(--line)}
.brand{position:absolute;left:269px;top:17px;display:flex;align-items:center}
.brand-dot{width:33px;height:33px;border-radius:50%;background:var(--accent)}
.brand-text{margin-left:9px}
.brand-name{font-size:27px;font-weight:900;letter-spacing:1.5px;color:var(--navy);line-height:1}
.brand-tag{font-size:8px;color:#444;margin-top:1px}
.btn{position:absolute;top:20px;height:26px;font-size:9px;text-align:center;line-height:26px;text-transform:uppercase}
.btn-ghost{background:#f1f1f1;border:1px solid #d6d6d6;color:#555}
.btn-account{left:686px;width:75px}
.btn-login{left:765px;width:74px}
.btn-signup{left:844px;width:74px;background:var(--accent);color:#fff;font-weight:700}

.nav{position:absolute;top:95px;left:269px;height:27px;display:flex;font-size:10px;color:#444}
.nav a{color:inherit;text-decoration:none;margin-right:38px;line-height:28px}
.nav a.active{color:var(--accent);position:relative}
.nav a.active::after{content:"";position:absolute;left:50%;margin-left:-5px;bottom:-1px;border:5px solid transparent;border-bottom-color:var(--accent);border-bottom-width:5px}

.hero{position:absolute;top:122px;left:0;width:1200px;height:317px;background:linear-gradient(180deg,#2c2a45 0%,#37354f 50%,#24223d 100%)}
.hero-line{position:absolute;top:215px;width:1200px;text-align:center;font-size:15px;color:#fff}
.hero-line em{font-style:normal;color:var(--accent)}
.dots{position:absolute;top:278px;left:578px;display:flex;gap:4px}
.dots i{width:7px;height:7px;border-radius:50%;background:#fff}
.dots i:first-child{background:var(--accent)}

.mega{position:absolute;top:133px;left:327px;width:359px;height:138px;background:#f5f4f4;border-top:3px solid var(--accent);box-shadow:0 2px 6px rgba(0,0,0,.25)}
.mega-photo{position:absolute;left:16px;top:17px;width:189px;height:85px;background:linear-gradient(160deg,#2a3350 0%,#8a6a3a 55%,#d9a84a 75%,#3d3b4d 100%)}
.mega-caption{position:absolute;left:16px;top:114px;font-size:10px;color:#333}
.mega-links{position:absolute;left:226px;top:17px;list-style:none;font-size:9.5px;color:#444}
.mega-links li{margin-bottom:7px}
.mega-links li.current{color:var(--accent);text-decoration:underline}

.welcome{position:absolute;top:439px;left:0;width:1200px;height:227px;background:var(--mist)}
.title{text-align:center;font-size:21px;font-weight:300;color:#444}
.title b{font-weight:700;color:var(--navy)}
.rule{width:106px;margin:6px auto 0;border-top:1px solid #999;border-bottom:1px solid #999;height:3px}
.welcome .title{margin-top:40px}
.welcome p{width:548px;margin:18px auto 0;font-size:8px;line-height:15px;text-align:center;color:#555}

.clients{position:absolute;top:666px;left:0;width:1200px;height:174px;background:var(--navy)}
.clients .title{margin-top:34px;color:#fff}
.clients .title b{color:#fff}
.clients .rule{border-color:#bbb}
.client-strip{position:absolute;left:269px;top:83px;width:649px;height:59px;background:#fff;display:flex;align-items:center;justify-content:space-around;padding:0 10px}
.client{font-size:12px;font-weight:700;color:#8a8a8a;display:flex;align-items:center;gap:5px}
.client .mark{width:12px;height:12px;border-radius:50%;background:#9a9a9a}

.social{position:absolute;top:840px;left:0;width:1200px;height:35px;background:#fff}
.social-links{position:absolute;left:269px;top:10px;display:flex;gap:24px;font-size:12px;font-weight:700}
.s-a{color:#222}.s-b{color:#c62a22}.s-c{color:var(--accent)}
.subscribe{position:absolute;left:650px;top:9px;display:flex}
.subscribe .field{width:186px;height:22px;border:1px solid var(--accent);font-size:8.5px;color:var(--accent);padding:6px 7px}
.subscribe .go{width:81px;height:22px;background:var(--accent);color:#fff;font-size:9px;font-weight:700;text-align:center;line-height:22px;margin-left:2px}

.footer{position:absolute;top:875px;left:0;width:1200px;height:208px;background:var(--footer)}
.col{position:absolute;top:19px;width:105px}
.col h4{font-size:11px;font-weight:400;color:#222;padding-bottom:6px;border-bottom:3px double #aaa}
.col ul{list-style:none;margin-top:12px;font-size:8.5px;color:#444}
.col li{margin-bottom:8px}
.col li.current{color:var(--accent);text-decoration:underline}
.contact{position:absolute;left:741px;top:0;width:177px;height:208px;background:var(--navy-deep);color:#fff;padding:18px 0 0 25px;font-size:8.5px}
.contact .brand-mini{display:flex;align-items:center;margin-left:-4px}
.contact .brand-mini .dot{width:23px;height:23px;border-radius:50%;background:#fff}
.contact .brand-mini .nm{font-size:18px;font-weight:900;letter-spacing:1px;margin-left:6px;line-height:1}
.contact .brand-mini .tg{font-size:6px;margin-left:6px;color:#ccc}
.contact .addr{line-height:14px;margin-top:10px}
.contact .row{display:flex;align-items:center;margin-top:10px;margin-left:-2px}
.contact .row svg{margin-right:8px}
.contact .addr2{line-height:14px;margin-top:19px}

.copyright{position:absolute;top:1083px;left:0;width:1200px;height:37px;border-bottom:1px solid var(--line);text-align:center;font-size:8px;color:#777;line-height:37px}
</style>
</head>
<body>
<div class="page">

  <div class="topbar">
    <div class="phone">T +31 (0) 20 5550 184</div>
    <div class="lang">ENG<span></span></div>
    <div class="search">Search</div>
  </div>

  <header class="header">
    <div class="brand">
      <div class="brand-dot"></div>
      <div class="brand-text">
        <div class="brand-name">NORVENTA</div>
        <div class="brand-tag">Real-time reasoning solutions</div>
      </div>
    </div>
    <div class="btn btn-ghost btn-account">Account</div>
    <div class="btn btn-ghost btn-login">Login</div>
    <div class="btn btn-signup">Sign up</div>
  </header>

  <nav class="nav">
    <a>Home</a><a class="active">Industry</a><a>Telecom</a><a>Power</a><a>Utilities</a><a>Infra</a><a>Store</a>
  </nav>

  <section class="hero" role="img" aria-label="Looking up at dark glass office towers against a cloudy sky">
    <div class="hero-line">A perfect Blend of <em>CREATIVITY</em> with <em>SIMPLICITY</em> enhancing your business</div>
    <div class="dots"><i></i><i></i><i></i></div>
  </section>

  <div class="mega">
    <div class="mega-photo" role="img" aria-label="Refinery plant lit up at night"></div>
    <div class="mega-caption">Koptekest 5</div>
    <ul class="mega-links">
      <li>Alarm Management</li>
      <li class="current">Asset Management</li>
      <li>Predictive Maintenence</li>
      <li>Logic Design</li>
    </ul>
  </div>

  <section class="welcome">
    <h2 class="title">Welcome to <b>NORVENTA</b></h2>
    <div class="rule"></div>
    <p>Companies have invested to get data out of processes. New technologies have been developed to get real-time data out of the harshest places, like oil-well drill heads or the Great Barrier Riff. Data in itself means nothing without the context the data is collected in. Example: data from equipment under maintenance does not provide information to operations. Information - data which is valid and meaningful - can overwhelm any user without the proper knowledge to interpret this information. NORVENTA technology enables easy application of such knowledge in a comprehensible – visual – representation and makes hypothetical reasoning with information possible providing meaningful advisories to subscribers when they need it or when it is required that they are made aware of a situation which requires their attention.</p>
  </section>

  <section class="clients">
    <h2 class="title">Our <b>CLIENTS</b></h2>
    <div class="rule"></div>
    <div class="client-strip">
      <div class="client"><span class="mark"></span>Petrava</div>
      <div class="client"><span class="mark"></span>Kelvor</div>
      <div class="client">Brouwmark</div>
      <div class="client">Delmont Chem</div>
      <div class="client">Nordhav Oil</div>
      <div class="client">Qarim</div>
      <div class="client"><span class="mark"></span>Conchex</div>
    </div>
  </section>

  <div class="social">
    <div class="social-links">
      <span class="s-a">Chirpline</span>
      <span class="s-b">ViewCast</span>
      <span class="s-c">ProLink</span>
    </div>
    <div class="subscribe">
      <div class="field">Enter Your Email Address</div>
      <div class="go">SUBSCRIBE</div>
    </div>
  </div>

  <footer class="footer">
    <div class="col" style="left:269px">
      <h4>Solutions</h4>
      <ul><li>NVA Alarm Reporting</li><li class="current">NVA Alarm Analysis</li><li>NVA Alarm Expert</li><li>USE</li></ul>
    </div>
    <div class="col" style="left:389px">
      <h4>Industries</h4>
      <ul><li>Industry</li><li>Telcom</li><li>Power</li><li>Utilities</li><li>Infra</li></ul>
    </div>
    <div class="col" style="left:509px">
      <h4>About Us</h4>
      <ul><li>Company</li><li>Overview</li><li>Leadership</li><li>Partners</li><li>Location</li></ul>
    </div>
    <div class="col" style="left:627px">
      <h4>News</h4>
      <ul><li>Product News</li><li>Partner News</li><li>Events</li><li>Press Releases</li><li>Vacancies</li></ul>
    </div>
    <div class="contact">
      <div class="brand-mini"><span class="dot"></span><div><div class="nm">NORVENTA</div><div class="tg">Real-time reasoning solutions</div></div></div>
      <div class="addr">#123, Street Name, City Name<br>Country CH - 1234</div>
      <div class="row">
        <svg width="20" height="20" viewBox="0 0 20 20"><circle cx="10" cy="10" r="9" fill="none" stroke="#fff" stroke-width="1"/><path d="M7 5.5l2 2-1 1.2c.6 1.4 1.6 2.4 3 3l1.2-1 2 2-1.2 1.3c-3.4-.4-6.3-3.3-6.7-6.7z" fill="#fff"/></svg>
        (44) 555 010 2468
      </div>
      <div class="row">
        <svg width="20" height="20" viewBox="0 0 20 20"><circle cx="10" cy="10" r="9" fill="none" stroke="#fff" stroke-width="1"/><rect x="5.5" y="7" width="9" height="6.5" fill="#fff"/><path d="M5.5 7l4.5 3.5L14.5 7" fill="none" stroke="#17152e" stroke-width="0.9"/></svg>
        hello@norventa.test
      </div>
      <div class="addr2">#123, Street Name, City Name<br>Country CH - 1234</div>
    </div>
  </footer>

  <div class="copyright">Copyright 2015 NORVENTA. All Rights Reserved.</div>
</div>
</body>
</html>
```